Calvanto Group Real Estate Company business cards

New business card design, we are generally happy with the basic layout of the existing front of business card, (feel free to change) but require a head shot photo on the back side.

http://www.calvanto.com.au/

Attached logos, and existing business card

------------------------------

Target Market(s)

Real estate

Industry/Entity Type

Real Estate

Contact Information for Business Card

Standard size double sided

Font styles to use
Other font styles liked:
• Futura

Requirements
Must have
• Photo head shot on the back side
Nice to have
• yes
Should not have
• No

```html
<!DOCTYPE html>
<html lang="en">
<head>
<meta charset="utf-8">
<title>Calvanto Group – Business Cards</title>
<link rel="stylesheet" href="https://fonts.googleapis.com/css2?family=Jost:wght@400;500;600;700&display=swap">
<style>
  :root {
    --purple: #2e1f6b;
    --orange: #f39a1e;
    --grey: #9a9aa6;
    --paper: #ffffff;
    --backdrop: #e6e6ea;
    --photo-light: #eef0f2;
    --photo-mid: #c9ccd3;
  }
  * { box-sizing: border-box; margin: 0; padding: 0; }
  html, body { width: 1200px; height: 900px; overflow: hidden; }
  body {
    background: var(--backdrop);
    font-family: "Jost", "Futura", sans-serif;
    position: relative;
  }
  .card {
    position: absolute;
    width: 560px;
    height: 342px;
    background: var(--paper);
    box-shadow: 0 10px 30px rgba(0,0,0,0.18);
    overflow: hidden;
  }
  .card--front { left: 250px; top: 70px; }
  .card--back { left: 390px; top: 480px; }

  /* Front */
  .front-brand {
    position: absolute; left: 0; right: 0; top: 92px;
    text-align: center;
  }
  .wordmark {
    font-weight: 500;
    color: var(--purple);
    font-size: 74px;
    line-height: 1;
    letter-spacing: -1px;
  }
  .wordmark-sub {
    display: block;
    font-size: 11px;
    letter-spacing: 7px;
    color: var(--grey);
    text-align: right;
    margin-right: 118px;
    margin-top: 2px;
  }
  .services {
    margin-top: 20px;
    font-size: 17px;
    font-weight: 600;
    letter-spacing: 2.5px;
    color: var(--purple);
  }
  .services .sep { color: var(--orange); margin: 0 6px; }
  .front-web {
    position: absolute; left: 0; right: 0; bottom: 30px;
    text-align: center;
    font-size: 18px;
    color: var(--purple);
    font-weight: 600;
    letter-spacing: 0.5px;
  }
  .front-web .accent { color: var(--orange); font-weight: 400; }

  /* Back */
  .back-shape { position: absolute; inset: 0; }
  .back-brand { position: absolute; left: 34px; top: 84px; }
  .back-brand .wordmark { font-size: 50px; }
  .back-brand .wordmark-sub { font-size: 9px; letter-spacing: 5px; margin-right: 2px; }
  .tagline {
    font-size: 18px;
    color: var(--purple);
    margin-top: 2px;
  }
  .person { position: absolute; left: 36px; top: 200px; color: var(--paper); }
  .person-name { font-size: 24px; font-weight: 700; letter-spacing: 1px; line-height: 1; }
  .person-role { font-size: 13px; color: var(--orange); font-weight: 500; letter-spacing: 0.5px; margin-top: 4px; line-height: 1.2; }
  .contact-list { list-style: none; margin-top: 6px; font-size: 13px; line-height: 1.4; }
  .contact-list li { display: flex; align-items: center; gap: 7px; }
  .contact-label { color: var(--orange); }
  .contact-icon { width: 11px; height: 11px; flex: none; }
  .headshot {
    position: absolute; left: 330px; top: 20px;
    width: 200px; height: 200px; border-radius: 50%;
    border: 6px solid var(--paper);
    background: radial-gradient(circle at 50% 40%, var(--photo-light), var(--photo-mid));
  }
</style>
</head>
<body>

<section class="card card--front" aria-label="Business card front">
  <div class="front-brand">
    <div class="wordmark">calvanto</div>
    <span class="wordmark-sub">GROUP</span>
    <p class="services">Buy<span class="sep">|</span>Sell<span class="sep">|</span>Rent</p>
  </div>
  <p class="front-web"><span class="accent">www.</span>calvanto.com<span class="accent">.au</span></p>
</section>

<section class="card card--back" aria-label="Business card back">
  <svg class="back-shape" width="560" height="342" viewBox="0 0 560 342" aria-hidden="true">
    <path d="M0 188 H300 L560 96 V342 H0 Z" fill="var(--purple)"/>
  </svg>
  <div class="headshot" role="img" aria-label="Head shot photo of the agent"></div>
  <div class="back-brand">
    <div class="wordmark">calvanto</div>
    <span class="wordmark-sub">GROUP</span>
    <p class="tagline">your next home starts here</p>
  </div>
  <div class="person">
    <p class="person-name">DANIEL TRAN</p>
    <p class="person-role">DIRECTOR</p>
    <ul class="contact-list">
      <li><span class="contact-label">ABN:</span> 12 408 316 925</li>
      <li>
        <svg class="contact-icon" viewBox="0 0 12 12" aria-hidden="true"><rect x="3" y="0.5" width="6" height="11" rx="1" fill="none" stroke="var(--orange)" stroke-width="1.2"/><circle cx="6" cy="9.5" r="0.7" fill="var(--orange)"/></svg>
        0400 555 218
      </li>
      <li>
        <svg class="contact-icon" viewBox="0 0 12 12" aria-hidden="true"><rect x="0.6" y="2.5" width="10.8" height="7" fill="none" stroke="var(--orange)" stroke-width="1.2"/><path d="M0.6 2.5 L6 6.6 L11.4 2.5" fill="none" stroke="var(--orange)" stroke-width="1.2"/></svg>
        daniel.tran@calvanto.com.au
      </li>
      <li>
        <svg class="contact-icon" viewBox="0 0 12 12" aria-hidden="true"><circle cx="6" cy="6" r="5.2" fill="none" stroke="var(--orange)" stroke-width="1.2"/><ellipse cx="6" cy="6" rx="2.3" ry="5.2" fill="none" stroke="var(--orange)" stroke-width="1"/><path d="M0.8 6 H11.2" stroke="var(--orange)" stroke-width="1"/></svg>
        www.calvanto.com.au
      </li>
    </ul>
  </div>
</section>

</body>
</html>
```